Business card for Sports Apparel business

DOUBLE SIDED DESIGN
We need business cards for a new sports apparel business. We are developing a protective headband for soccer initially.
Torvalle is focused on designing and developing head protection products to reduce the likelihood of concussion when playing sports. Exploring and understanding medical insights, material science research, current and former players experiences and governing bodies guidelines has allowed Torvalle to develop the safety, style, form and function requirements of a suitable product to bring to market.
Target Market(s)
Mums buying kits for the sons and daughters. Amateur footballers.
Industry/Entity Type
Sporting Good
Contact Information for Business Card
Martin Ashworth - CEO
Mobile: +44 7431589027
Email: martin@torvalle.co.uk
Tel: 0208 5519372
Helena Pargeter - COO
Mob: +44 7385 640117
Email: helena@torvalle.co.uk
Tel: 0208 5519372
Duncan Farrow - CCO
Mob: +44 7564 293081
Email: duncan@torvalle.co.uk
Tel: 0208 5519372
Look and feel
Each slider illustrates characteristics of the customer's brand and the style your logo design should communicate.

```html
<!DOCTYPE html>
<html lang="en">
<head>
<meta charset="utf-8">
<title>Torvalle business card</title>
<link href="https://fonts.googleapis.com/css2?family=Montserrat:wght@400;500;600;700&display=swap" rel="stylesheet">
<style>
  :root {
    --brand-blue: #0b5b96;
    --brand-blue-dark: #084a7c;
    --card-white: #ffffff;
    --text-grey: #3a3d42;
    --backdrop: #3b3c3e;
  }
  * { box-sizing: border-box; margin: 0; padding: 0; }
  html, body {
    width: 1200px; height: 896px; overflow: hidden;
    background: var(--backdrop);
    font-family: "Montserrat", sans-serif;
  }
  .stage {
    position: relative; width: 1200px; height: 896px;
    display: flex; align-items: center; justify-content: center; gap: 120px;
  }
  .card {
    position: relative; width: 340px; height: 540px;
    border-radius: 28px; overflow: hidden;
    box-shadow: 0 14px 30px rgba(0,0,0,.35);
  }
  /* Front */
  .card-front {
    background: var(--brand-blue);
    display: flex; align-items: center; justify-content: center;
  }
  .front-wordmark {
    transform: rotate(-90deg);
    display: flex; align-items: center; gap: 14px;
    color: var(--card-white);
    font-weight: 600; font-size: 44px; letter-spacing: 3px;
    white-space: nowrap;
  }
  .mark-square {
    width: 18px; height: 18px; background: var(--card-white);
  }
  /* Back */
  .card-back { background: var(--card-white); }
  .edge-band {
    position: absolute; width: 16px; background: var(--brand-blue);
  }
  .edge-band.left { left: 0; top: 0; height: 78%; }
  .edge-band.right { right: 0; bottom: 0; height: 78%; }
  .back-wordmark {
    position: absolute; top: 80px; left: 0; right: 0;
    display: flex; justify-content: center; align-items: center; gap: 10px;
    color: var(--brand-blue);
    font-weight: 600; font-size: 30px; letter-spacing: 2px;
  }
  .back-wordmark .mark-square { width: 12px; height: 12px; background: var(--brand-blue); }
  .person { position: absolute; left: 60px; top: 248px; }
  .person-name {
    color: var(--brand-blue); font-weight: 700; font-size: 17px; letter-spacing: 1.5px;
    text-transform: uppercase;
  }
  .person-role { color: var(--text-grey); font-size: 13px; letter-spacing: 1px; margin-top: 2px; }
  .person-rule { width: 24px; height: 2px; background: var(--brand-blue); margin-top: 18px; }
  .contact-list { list-style: none; position: absolute; left: 60px; top: 350px; }
  .contact-list li {
    display: flex; align-items: center; gap: 10px;
    color: var(--text-grey); font-size: 13.5px; line-height: 22px; letter-spacing: .4px;
  }
  .contact-list svg { width: 12px; height: 12px; fill: none; stroke: var(--brand-blue); stroke-width: 1.6; }
  .web-domain { color: var(--brand-blue); }
</style>
</head>
<body>
<main class="stage">
  <section class="card card-front" aria-label="Card front">
    <div class="front-wordmark"><span class="mark-square"></span>TORVALLE</div>
  </section>

  <section class="card card-back" aria-label="Card back">
    <span class="edge-band left"></span>
    <span class="edge-band right"></span>
    <div class="back-wordmark"><span class="mark-square"></span>TORVALLE</div>
    <div class="person">
      <p class="person-name">Helena Pargeter</p>
      <p class="person-role">COO</p>
      <div class="person-rule"></div>
    </div>
    <ul class="contact-list">
      <li><svg viewBox="0 0 12 12"><path d="M2 1.5l2 0 1 2.5-1.2 1a6 6 0 0 0 3.2 3.2l1-1.2 2.5 1v2a1 1 0 0 1-1 1A9 9 0 0 1 1 2.5a1 1 0 0 1 1-1z"/></svg>0208 5519372</li>
      <li><svg viewBox="0 0 12 12"><rect x="3" y="1" width="6" height="10" rx="1"/><path d="M5.3 9h1.4"/></svg>+44 7385 640117</li>
      <li><svg viewBox="0 0 12 12"><rect x="1" y="2.5" width="10" height="7" rx=".8"/><path d="M1.5 3l4.5 3.5L10.5 3"/></svg>helena@torvalle.co.uk</li>
      <li><svg viewBox="0 0 12 12"><circle cx="6" cy="6" r="5"/><path d="M1 6h10M6 1c2 2.5 2 7.5 0 10M6 1c-2 2.5-2 7.5 0 10"/></svg>www.<span class="web-domain">torvalle</span>.co.uk</li>
    </ul>
  </section>
</main>
</body>
</html>
```